Design a modern, classy & professional business card for an online real estate agency, specializing in medium-luxury properties in Thailand and later in Singapore and UK.

Possible design ideas so far: (not essential)

- curved corner(s) to the card, white on front & turquoise on back or visa versa.

- front of card - clear and simple, company name in metallic grey/monochrome, logo graphic & company name on front in spot UV or embossed/debossed effect.

- back of card - large, close-cropped, 'ghost' patterns of the C-shaped curves of logo, or company name repeated on back of card in spot UV.

Target Market(s)

- young to middle-aged professionals mainly (but ideally should design should suit all)

- UK, US,EU,AUS & ASIAN mainly (but ideally should design should suit all countries)

Industry/Entity Type

Real Estate

Requirements
Must have
• THEME:
- Luxurious & Modern
- Clean & striking
- Unique & creative

INFO:
- Logo & company name on front
- Contact details on back:

Tobias Hennlund
Managing Director

www.velmontestates.asia
www.velmontestates.co.uk

Tel: 083-274-6159
email: tobias@velmontestates.asia

(contact details can be displayed in any order as suites design.)

Nice to have
• - curved corner(s) to the card, white on front & turquoise on back or visa versa.

Should not have
• - No generic images of properties, palm trees/coconut trees etc.

- No other other bold colors, except for main turquoise, grey, metallic white & black theme.

- No obvious business card templates

```html
<!DOCTYPE html>
<html lang="en">
<head>
<meta charset="utf-8">
<title>Velmont Estates – Business Card Variations</title>
<link rel="stylesheet" href="https://fonts.googleapis.com/css2?family=Open+Sans:wght@400;600;700&display=swap">
<style>
  :root {
    --page-bg: #ecebe8;
    --card-white: #ffffff;
    --turquoise: #2db3ab;
    --turquoise-deep: #1e9890;
    --turquoise-light: #6fd6cf;
    --ink: #3d3d3d;
    --ink-soft: #8a8a8a;
    --rule: #d6d6d6;
    --shadow: rgba(0, 0, 0, 0.18);
  }
  * { box-sizing: border-box; margin: 0; padding: 0; }
  html, body { width: 1200px; height: 2400px; overflow: hidden; }
  body {
    background: var(--page-bg);
    font-family: "Open Sans", Arial, sans-serif;
    color: var(--ink);
  }
  .variation {
    position: relative;
    width: 1200px;
    height: 800px;
  }
  .card {
    position: absolute;
    top: 250px;
    width: 520px;
    height: 300px;
    border-radius: 22px;
    box-shadow: 0 10px 28px var(--shadow);
    overflow: hidden;
  }
  .card-front { left: 60px; background: var(--card-white); }
  .card-back {
    left: 620px;
    background: linear-gradient(135deg, var(--turquoise-deep) 0%, var(--turquoise) 45%, var(--turquoise-light) 70%, var(--turquoise) 100%);
  }
  .card-back .pattern-area {
    position: absolute;
    inset: 0;
    background: radial-gradient(circle at 70% 40%, rgba(255,255,255,0.22), rgba(255,255,255,0) 60%);
  }

  .brand {
    position: absolute;
    display: flex;
    align-items: center;
    gap: 10px;
  }
  .brand-mark {
    width: 34px;
    height: 34px;
    background: var(--turquoise);
    border-radius: 4px;
  }
  .brand-name {
    font-size: 24px;
    font-weight: 600;
    color: var(--turquoise);
    letter-spacing: 0.2px;
  }

  .person { position: absolute; }
  .person-name { font-size: 15px; font-weight: 700; color: var(--ink); }
  .person-title { font-size: 11px; color: var(--ink-soft); margin-top: 2px; }

  .divider {
    position: absolute;
    width: 1px;
    background: var(--rule);
  }
  .contacts {
    position: absolute;
    list-style: none;
    font-size: 11px;
    line-height: 19px;
    color: var(--ink);
  }
  .contacts li { display: flex; align-items: center; gap: 7px; }
  .contacts .bullet {
    width: 8px; height: 8px;
    background: var(--turquoise);
    border-radius: 1px;
    flex: none;
  }
  .contacts .spacer { width: 8px; flex: none; }
  .contacts.align-right li { justify-content: flex-end; }

  /* Variation one */
  .v1 .brand { left: 40px; top: 34px; }
  .v1 .person { left: 40px; top: 88px; }
  .v1 .divider { left: 250px; top: 150px; height: 110px; }
  .v1 .contacts { left: 270px; top: 160px; }

  /* Variation two */
  .v2 .person { left: 40px; top: 42px; }
  .v2 .brand { left: 250px; top: 70px; }
  .v2 .divider { left: 220px; top: 140px; height: 110px; }
  .v2 .contacts { left: 240px; top: 150px; }

  /* Variation three */
  .v3 .brand { left: 40px; top: 40px; }
  .v3 .person { right: 40px; top: 40px; text-align: right; }
  .v3 .contacts { right: 40px; top: 150px; }
</style>
</head>
<body>

<section class="variation v1">
  <div class="card card-front">
    <div class="brand"><span class="brand-mark"></span><span class="brand-name">Velmont Estates</span></div>
    <div class="person">
      <p class="person-name">Tobias Hennlund</p>
      <p class="person-title">Managing Director</p>
    </div>
    <div class="divider"></div>
    <ul class="contacts">
      <li><span class="bullet"></span>083-274-6159</li>
      <li><span class="bullet"></span>tobias@velmontestates.asia</li>
      <li><span class="spacer"></span>www.velmontestates.asia</li>
      <li><span class="spacer"></span>www.velmontestates.co.uk</li>
    </ul>
  </div>
  <div class="card card-back">
    <div class="pattern-area" role="img" aria-label="Ghosted pattern of interlocking rings in spot UV over turquoise"></div>
  </div>
</section>

<section class="variation v2">
  <div class="card card-front">
    <div class="person">
      <p class="person-name">Tobias Hennlund</p>
      <p class="person-title">Managing Director</p>
    </div>
    <div class="brand"><span class="brand-mark"></span><span class="brand-name">Velmont Estates</span></div>
    <div class="divider"></div>
    <ul class="contacts">
      <li><span class="bullet"></span>083-274-6159</li>
      <li><span class="bullet"></span>tobias@velmontestates.asia</li>
      <li><span class="spacer"></span>www.velmontestates.asia</li>
      <li><span class="spacer"></span>www.velmontestates.co.uk</li>
    </ul>
  </div>
  <div class="card card-back">
    <div class="pattern-area" role="img" aria-label="Ghosted pattern of interlocking rings in spot UV over turquoise"></div>
  </div>
</section>

<section class="variation v3">
  <div class="card card-front">
    <div class="brand"><span class="brand-mark"></span><span class="brand-name">Velmont Estates</span></div>
    <div class="person">
      <p class="person-name">Tobias Hennlund</p>
      <p class="person-title">Managing Director</p>
    </div>
    <ul class="contacts align-right">
      <li>tobias@velmontestates.asia<span class="bullet"></span></li>
      <li>083-274-6159<span class="bullet"></span></li>
      <li>www.velmontestates.asia<span class="spacer"></span></li>
      <li>www.velmontestates.co.uk<span class="spacer"></span></li>
    </ul>
  </div>
  <div class="card card-back">
    <div class="pattern-area" role="img" aria-label="Ghosted pattern of interlocking rings in spot UV over turquoise"></div>
  </div>
</section>

</body>
</html>
```